BRISKEL Need a luxury modern business card designed.

Need a luxury modern business card designed. refer to the uploaded files for the company name and logo in the zip file under source files. i will making my descion on monday. so please send in before then so if we need to edit we will have the time. we have a trade show coming up and im on a deadline for printer.

Target Market(s)

high end clients

Contact Information for Business Card

Company nAme and logo. Tobias Fennick Co-Founder / Project Manager Office # 555-318-7094 Cell # 555-642-1586 BRISKEL.CA Tobias@briskel-example.ca

Font styles to use
Other font styles liked:
• Modern

Requirements
Must have
• Company name and logo, contact info, using the black, gold and white color scheme.

```html
<!DOCTYPE html>
<html lang="en">
<head>
<meta charset="utf-8">
<title>BRISKEL Business Card</title>
<link href="https://fonts.googleapis.com/css2?family=Montserrat:wght@300;400;500;600&display=swap" rel="stylesheet">
<style>
  :root {
    --backdrop: #141414;
    --card: #303030;
    --gold: #b3a36a;
    --white: #f4f4f2;
    --divider: #8f835a;
  }
  * { margin: 0; padding: 0; box-sizing: border-box; }
  html, body {
    width: 1200px; height: 900px; overflow: hidden;
    background: var(--backdrop);
    font-family: "Montserrat", sans-serif;
  }
  .stage { position: relative; width: 1200px; height: 900px; }
  .card {
    position: absolute; left: 290px; width: 620px; height: 354px;
    background: var(--card);
    border: 3px solid var(--gold);
  }
  .card-front { top: 50px; }
  .card-back { top: 476px; }

  .front-wordmark {
    position: absolute; right: 56px; top: 110px;
    font-weight: 300; font-size: 52px; letter-spacing: 10px;
    color: var(--white);
  }

  .back-brand {
    position: absolute; left: 44px; top: 150px;
    font-weight: 300; font-size: 38px; letter-spacing: 7px;
    color: var(--white);
  }
  .divider {
    position: absolute; left: 288px; width: 2px; background: var(--divider);
  }
  .divider-top { top: 92px; height: 44px; }
  .divider-bottom { top: 156px; height: 110px; }

  .contact-name {
    position: absolute; left: 310px; top: 90px;
    font-weight: 600; font-size: 22px; letter-spacing: 1.5px;
    color: var(--gold); text-transform: uppercase;
  }
  .contact-title {
    position: absolute; left: 310px; top: 120px;
    font-weight: 400; font-size: 16px; color: var(--white);
  }
  .contact-list {
    position: absolute; left: 310px; top: 158px;
    list-style: none;
  }
  .contact-list li {
    display: flex; align-items: center; gap: 12px;
    height: 26px; font-size: 17px; font-weight: 400; color: var(--white);
  }
  .contact-list svg { width: 16px; height: 16px; flex: none; }
  .web-accent { color: var(--gold); }
</style>
</head>
<body>
<main class="stage">
  <section class="card card-front" aria-label="Card front">
    <div class="front-wordmark">BRISKEL</div>
  </section>

  <section class="card card-back" aria-label="Card back">
    <div class="back-brand">BRISKEL</div>

    <span class="divider divider-top"></span>
    <span class="divider divider-bottom"></span>

    <div class="contact-name">Tobias Fennick</div>
    <div class="contact-title">Co-Founder | Project Manager</div>

    <ul class="contact-list">
      <li>
        <svg viewBox="0 0 16 16" fill="none" stroke="#f4f4f2" stroke-width="1.3" aria-hidden="true">
          <circle cx="8" cy="8" r="7"/>
          <path d="M5.5 4.5l1.5 1.5-1 1c.6 1.2 1.6 2.2 2.8 2.8l1-1 1.7 1.5-1 1.2c-2.8-.4-5.6-3.2-6-6z"/>
        </svg>
        555-318-7094
      </li>
      <li>
        <svg viewBox="0 0 16 16" fill="none" stroke="#f4f4f2" stroke-width="1.3" aria-hidden="true">
          <rect x="4.5" y="1.5" width="7" height="13" rx="1.2"/>
          <line x1="7" y1="12.3" x2="9" y2="12.3"/>
        </svg>
        555-642-1586
      </li>
      <li>
        <svg viewBox="0 0 16 16" fill="none" stroke="#f4f4f2" stroke-width="1.3" aria-hidden="true">
          <rect x="1.5" y="3.5" width="13" height="9"/>
          <path d="M1.5 3.5l6.5 5 6.5-5"/>
        </svg>
        Tobias@briskel-example.ca
      </li>
      <li>
        <svg viewBox="0 0 16 16" fill="none" stroke="#f4f4f2" stroke-width="1.2" aria-hidden="true">
          <circle cx="8" cy="8" r="6.5"/>
          <ellipse cx="8" cy="8" rx="3" ry="6.5"/>
          <line x1="1.5" y1="8" x2="14.5" y2="8"/>
        </svg>
        <span>WWW.<span class="web-accent">BRISKEL</span>.CA</span>
      </li>
    </ul>
  </section>
</main>
</body>
</html>
```